CONTACT US Page and design for website

We need a contact us page for our website. We would like it to have a message area, a map, our information, etc.

Please see the text attachment for what we are looking for. We need to have something that is creative and interesting, modern and professional.

We believe that a contact US page should be very creative because everyone clicks that to contact us. We want it to be super professional, attention grabbing, pleasing to the eye.

PLEASE KEEP THE HEADER AND FOOTER THE SAME, ONLY THE ACTUAL CONTACT US PAGE NEEDS TO BE WORKED ON. THANKS!
We are excited to work with designers for this project.

Target Market(s)

Clients in technology business

Industry/Entity Type

Information Technology

Number of Pages Required

1 page

Font styles to use
Serif

Requirements
Must have
• CHECK THE TEXT ATTACHMENT PLEASE
• Must stay within our design colors and theme.
Nice to have
• see attachment
Should not have
• it should be special

```html
<!DOCTYPE html>
<html lang="en">
<head>
<meta charset="utf-8">
<title>Contact Us – Norvex Tech</title>
<link href="https://fonts.googleapis.com/css2?family=Roboto:wght@300;400;500&family=Roboto+Condensed:wght@400;700&display=swap" rel="stylesheet">
<style>
:root{
  --teal:#3ccbb9;
  --teal-dark:#27a89b;
  --ink:#2c3b42;
  --text:#555;
  --line:#dcdcdc;
  --field:#f9f9f9;
  --foot:#9d9d9d;
  --foot-dark:#8e8e8e;
  --white:#fff;
}
*{box-sizing:border-box;margin:0;padding:0}
html,body{width:764px;height:1200px;overflow:hidden}
body{position:relative;background:var(--white);font-family:"Roboto",Arial,sans-serif;color:var(--text)}
.abs{position:absolute}
/* header */
.brand{left:40px;top:14px;display:flex;align-items:center;gap:8px}
.brand-mark{width:32px;height:32px;background:var(--teal);border-radius:50%}
.brand-name{font:400 20px "Roboto",sans-serif;letter-spacing:3px;color:var(--teal)}
.account{left:620px;top:0;width:106px;height:18px;background:#b0b0b0;border-radius:0 0 14px 14px;display:flex;font-size:6px;color:#fff;text-transform:uppercase}
.account span{flex:1;display:flex;align-items:center;justify-content:center}
.account span+span{background:#9a9a9a;border-radius:0 0 14px 0}
.contact-top{left:556px;top:26px;display:flex;align-items:center;gap:8px;font-size:8px;color:#555}
.round{width:22px;height:22px;border:1px solid #ccc;border-radius:50%;display:flex;align-items:center;justify-content:center}
.phone-top{font-size:11px;color:#333;margin-left:2px}
.nav{left:44px;top:64px;display:flex;gap:15px;font-size:7px;color:#444;letter-spacing:.2px}
.search{left:588px;top:62px;width:102px;height:16px;border:1px solid #ccc;border-radius:8px;font-size:6px;padding:4px 12px;color:#555}
.cart{left:699px;top:60px;width:20px;height:20px}
.rule{left:0;top:55px;width:764px;height:1px;background:var(--line)}
.rule2{left:0;top:82px;width:764px;height:1px;background:var(--line)}
.crumb{left:0;top:84px;width:764px;height:30px;background:linear-gradient(90deg,var(--teal-dark),var(--teal) 40%,var(--teal-dark));font:400 8px "Roboto Condensed",sans-serif;color:#fff;padding:11px 43px}
.crumb em{font-style:normal;color:#2c5d59}
.map{left:0;top:114px;width:764px;height:260px;background:linear-gradient(135deg,#e9e7e2,#dedcd6)}
/* contact form */
h2.h-big{left:37px;top:420px;font:400 17px "Roboto",sans-serif;color:var(--ink);letter-spacing:.5px}
.underline{height:2px;width:50px;background:var(--teal)}
h3.h-sub{font:500 12px "Roboto Condensed",sans-serif;color:var(--ink);letter-spacing:.5px}
.field{left:38px;width:320px;height:22px;background:var(--field);border:1px solid var(--line);font-size:7.5px;color:#666;padding:7px 10px}
.submit{left:38px;top:642px;width:59px;height:20px;background:var(--teal);color:#fff;font-size:8px;text-align:center;line-height:20px;border-radius:1px}
.hours{left:414px;top:470px;list-style:none;font-size:9.5px;color:#444}
.hours li{height:19px;display:flex;align-items:center;gap:10px}
.dot{width:7px;height:7px;border:1.2px solid var(--teal);border-radius:50%}
.social{display:flex;gap:3px}
.social span{width:21px;height:21px;border:1px solid #888;border-radius:50%}
.support{left:414px;top:582px;width:312px;height:56px;background:#f5f5f5;border:1px solid #e4e4e4;display:flex;align-items:center;gap:14px;padding-left:16px;font-size:9px;color:#333;line-height:15px}
/* info band */
.band{left:0;top:714px;width:764px;height:194px;background:linear-gradient(90deg,var(--teal-dark),var(--teal) 45%,var(--teal-dark))}
.band-title{left:0;top:746px;width:764px;text-align:center;font:400 19px "Roboto",sans-serif;color:#fff;letter-spacing:.5px}
.card{top:791px;height:74px;border:1px solid rgba(255,255,255,.85);color:#fff;padding:10px 16px}
.card h4{font:400 13px "Roboto",sans-serif;letter-spacing:.3px;margin-bottom:9px}
.card p{font-size:9.5px;display:flex;align-items:center;gap:10px;height:19px}
/* footer */
.foot{left:0;top:908px;width:764px;height:182px;background:var(--foot);color:#fff}
.foot-dark{left:0;top:1090px;width:764px;height:110px;background:var(--foot-dark);color:#fff}
.about{left:200px;top:927px;width:400px;text-align:center;font-size:8.2px;line-height:12px;color:#fff}
.hr{height:1px;background:rgba(255,255,255,.25)}
.addr{top:994px;font-size:8.2px;color:#fff;display:flex;gap:7px;line-height:12px}
.links{top:1034px;font-size:9.8px;color:#fff}
.mini{left:500px;top:1050px;width:92px;text-align:center;font-size:5.5px;line-height:8.8px;color:#fff}
.fsocial{left:310px;top:1102px;display:flex;gap:10px}
.fsocial span{width:24px;height:24px;border:1px solid rgba(255,255,255,.6);border-radius:50%}
.copy{left:340px;top:1148px;display:flex;gap:8px;align-items:center;font-size:7.5px;line-height:11px;color:#fff}
.copy i{width:14px;height:14px;background:#d5d5d5;display:block}
.tab{left:669px;top:1183px;width:95px;height:17px;background:var(--teal);color:#fff;font:700 7.5px "Roboto",sans-serif;padding:4px 6px;border:1px solid #fff;border-bottom:none}
</style>
</head>
<body>
<header>
  <div class="abs brand"><span class="brand-mark"></span><div class="brand-name">NORVEX TECH</div></div>
  <div class="abs account"><span>Sign up</span><span>Login</span></div>
  <div class="abs contact-top">
    <span class="round"><svg width="9" height="8" viewBox="0 0 9 8"><path d="M1 1h7v4H4L2 7V5H1z" fill="#666"/></svg></span>
    <span>LIVE CHAT</span>
    <span class="round"><svg width="9" height="9" viewBox="0 0 10 10"><path d="M2 1l2 2-1 1.5c.8 1.5 1.5 2.2 3 3L7.5 6l2 2-1.3 1.5C4.5 9 1 5.5.5 1.8z" fill="var(--teal)"/></svg></span>
    <span class="phone-top">555-240-1180</span>
  </div>
  <div class="abs rule"></div>
  <nav class="abs nav"><span>SERVERS</span><span>WORKSTATIONS</span><span>COMPONENTS</span><span>VIRTUAL REALITY</span><span>DRONES</span><span>ABOUT US</span><span>BLOG</span><span>RESOURCES</span><span>CONTACT US</span></nav>
  <div class="abs search">Search</div>
  <svg class="abs" style="left:674px;top:66px" width="9" height="9" viewBox="0 0 10 10"><circle cx="4" cy="4" r="3" fill="none" stroke="var(--teal)" stroke-width="1.4"/><path d="M6.2 6.2L9 9" stroke="var(--teal)" stroke-width="1.4"/></svg>
  <svg class="abs cart" viewBox="0 0 20 20"><circle cx="10" cy="10" r="9.3" fill="none" stroke="var(--teal)" stroke-width="1.2"/><rect x="6" y="8" width="8" height="5" fill="var(--teal)"/><rect x="7" y="6" width="6" height="2" fill="none" stroke="var(--teal)"/></svg>
  <div class="abs rule2"></div>
</header>

<div class="abs crumb">HOME / <em>CONTACT US</em></div>
<div class="abs map" role="img" aria-label="Street map showing the office headquarters location"></div>

<main>
  <h2 class="abs h-big">CONTACT US</h2>
  <div class="abs underline" style="left:38px;top:444px"></div>
  <div class="abs field" style="top:466px">Name</div>
  <div class="abs field" style="top:493px">Phone No</div>
  <div class="abs field" style="top:520px">E-mail</div>
  <div class="abs field" style="top:547px;height:83px">Message</div>
  <div class="abs submit">SUBMIT</div>

  <h3 class="abs h-sub" style="left:414px;top:423px">HOURS OF OPERATION</h3>
  <div class="abs underline" style="left:414px;top:444px;width:45px"></div>
  <ul class="abs hours">
    <li><span class="dot"></span>Monday: 8:00am- 5:00pm</li>
    <li><span class="dot"></span>Tuesday: 8:00am- 5:00pm</li>
    <li><span class="dot"></span>Wednesday: 8:00am- 5:00pm</li>
    <li><span class="dot"></span>Thursday: 8:00am- 5:00pm</li>
    <li><span class="dot"></span>Friday: 8:00am- 5:00pm</li>
  </ul>

  <h3 class="abs h-sub" style="left:621px;top:423px">STAY CONNECTED</h3>
  <div class="abs underline" style="left:621px;top:444px;width:45px"></div>
  <div class="abs social" style="left:620px;top:467px"><span></span><span></span><span></span><span></span></div>

  <div class="abs support">
    <svg width="28" height="28" viewBox="0 0 28 28"><circle cx="15" cy="13" r="10" fill="none" stroke="var(--teal)" stroke-width="2"/><text x="15" y="16.5" font-size="9" font-weight="700" fill="var(--teal)" text-anchor="middle" font-family="Roboto,sans-serif">24</text><path d="M2 16c1 5 4 8 9 10l2-3-3-2-1 1c-2-1-3-2-4-4l1-1-2-3z" fill="var(--teal)"/></svg>
    <div>Our dedicated customer service representatives<br>are available 24/7 by phone.</div>
  </div>
</main>

<section>
  <div class="abs band"></div>
  <h2 class="abs band-title">CONTACT INFO</h2>
  <div class="abs card" style="left:110px;width:171px"><h4>GENERAL INQUIRIES</h4><p>&#9990;&nbsp;(555)240-1180</p><p>&#9993;&nbsp;info@norvextech.com</p></div>
  <div class="abs card" style="left:290px;width:170px"><h4>SALES INQUIRIES</h4><p>&#9990;&nbsp;(555)240-1180</p><p>&#9993;&nbsp;sales@norvextech.com</p></div>
  <div class="abs card" style="left:468px;width:186px"><h4>PURCHASING INQUIRIES</h4><p>&#9990;&nbsp;(555)240-1181</p><p>&#9993;&nbsp;purchasing@norvextech.com</p></div>
</section>

<footer>
  <div class="abs foot"></div>
  <p class="abs about">Based in Harlow Park California, Norvex Tech offers custom servers, storage, and workstations for local businesses in Los Angeles, Beverly Hills, Thousand Oaks, Ventura, Orange County, Santa Barbara, Oxnard, Irvine, Anaheim, and San Diego. Norvex Tech also offers such products to clients throughout the United States and Worldwide.</p>
  <div class="abs hr" style="left:206px;top:983px;width:390px"></div>
  <div class="abs addr" style="left:207px"><span>&#9906;</span><span>4120 Delmar Ave.<br>Harlow Park, CA 90412</span></div>
  <div class="abs addr" style="left:342px"><span>&#9990;</span><span>555-240-1180</span></div>
  <div class="abs addr" style="left:458px"><span>&#9993;</span><span>sales@norvextech.com</span></div>
  <span class="abs links" style="left:163px">Computer Hardware</span>
  <span class="abs links" style="left:284px">Drones</span>
  <span class="abs links" style="left:338px">Virtual Reality</span>
  <span class="abs links" style="left:427px">About Us</span>
  <span class="abs links" style="left:503px">Customer Support</span>
  <p class="abs mini">Terms and Conditions<br>Warranty Information<br>Contact Us<br>Return Policy</p>
  <div class="abs foot-dark"></div>
  <div class="abs fsocial"><span></span><span></span><span></span><span></span></div>
  <div class="abs hr" style="left:80px;top:1140px;width:604px"></div>
  <div class="abs copy"><i></i><span>Norvex Tech, LLC.<br>Copyright © 2017</span></div>
  <div class="abs tab">Leave a message</div>
</footer>
</body>
</html>
```